AnswerCraft Website Redesign

I'm looking to redesign our website AnswerCraft.com. The main goal is to give it a fresh design that is easy on the eyes and pushes the users to creating an account.

Our platform is very simple and we only do one thing, we use ai to generate response to customer and product reviews.

See attached file to see the pricing section style.

On the homepage just under the hero section, I would like to include the wording:
"Write replies to the reviews you get on sites like:" then show the logos like we have on our register page: https://app.answercraft.com/public/index.php

Target Market(s)

Business owners with brick and morter business or any business or product that gets online reviews

Industry/Entity Type

reputation management

Number of Pages Required

2 page

Requirements
Must have
• Home page and pricing page

```html
<!DOCTYPE html>
<html lang="en">
<head>
<meta charset="utf-8">
<title>AnswerCraft – Write personalized responses to reviews</title>
<link href="https://fonts.googleapis.com/css2?family=Roboto:wght@400;500;700&family=Open+Sans:wght@400;600&display=swap" rel="stylesheet">
<style>
:root{
  --navy:#1f2f8f;
  --navy-deep:#18237a;
  --orange:#f7941d;
  --ink:#1c1c1c;
  --muted:#555a66;
  --line:#c9cbd3;
  --card-shadow:0 6px 22px rgba(30,40,90,.16);
  --footer:#151515;
  --white:#ffffff;
}
*{margin:0;padding:0;box-sizing:border-box}
html,body{width:1200px;height:4428px;overflow:hidden}
body{position:relative;background:var(--white);font-family:"Open Sans",sans-serif;color:var(--ink)}
.abs{position:absolute}
h1,h2,h3,.heading{font-family:"Roboto",sans-serif}
.accent{color:var(--orange)}
.btn{position:absolute;display:flex;align-items:center;justify-content:center;background:var(--orange);color:var(--white);font:700 13px "Roboto",sans-serif;text-transform:uppercase;border-radius:5px;letter-spacing:.2px}
.btn-outline{background:transparent;border:2px solid var(--white)}

/* header */
.brand{display:flex;align-items:center;gap:12px;font:700 32px "Roboto",sans-serif}
.brand-mark{width:38px;height:38px;border-radius:6px}
.site-header .brand{left:112px;top:36px;color:var(--navy)}
.site-header .brand-mark{background:var(--navy)}
.nav-link{position:absolute;top:48px;font:500 14px "Roboto",sans-serif;color:#333;text-transform:uppercase}

/* hero */
.hero{left:0;top:112px;width:1200px;height:558px;border-radius:0 0 170px 170px;overflow:hidden;
  background:linear-gradient(120deg,#8d97b8 0%,#6a779f 45%,#4a5684 70%,#7c87ad 100%)}
.hero-bubble{left:335px;top:189px;width:530px;height:378px;background:var(--white);border-radius:36px}
.hero-panel{left:368px;top:223px;width:464px;height:313px;background:var(--navy);border-radius:24px;text-align:center;color:var(--white)}
.hero-panel h1{margin-top:42px;font:700 36px/52px "Roboto",sans-serif;text-transform:uppercase}
.hero-dot{top:616px;width:10px;height:10px;border-radius:50%;background:var(--white)}

/* intro */
.intro{left:0;top:746px;width:1200px;text-align:center;font:500 25px/41px "Roboto",sans-serif}

/* feature cards */
.feature-card{top:1011px;width:300px;height:325px;background:var(--white);border-radius:6px;box-shadow:var(--card-shadow);text-align:center}
.feature-art{top:890px;width:260px;height:210px;border-radius:18px;background:linear-gradient(140deg,#e8ecfb,#c7d0f4 60%,#f9d7a8)}
.feature-card h3{margin-top:112px;font:500 18px "Roboto",sans-serif}
.feature-card p{margin:18px 20px 0;font:400 13.5px/25px "Open Sans",sans-serif;color:#444;height:75px;overflow:hidden}
.arrow{top:1152px;width:44px;height:44px;border-radius:50%}

/* how it works */
.how{left:0;top:1425px;width:1200px;height:581px;background:linear-gradient(90deg,#f1f1f3 0%,#e6e6ea 55%,#d3d5dc 100%)}
.how-title{left:0;top:1510px;width:1200px;text-align:center;font:500 29px "Roboto",sans-serif}
.how-sub{left:110px;top:1604px;font:500 19px "Roboto",sans-serif;color:var(--navy)}
.how-text{left:110px;top:1656px;width:410px;font:400 14.5px/25px "Open Sans",sans-serif;color:#444}
.how-point{left:112px;width:412px;border-bottom:1px solid #8a8c94;padding:0 0 22px 44px;font:500 19px "Roboto",sans-serif;position:absolute}
.how-point::before{content:"";position:absolute;left:13px;top:8px;width:10px;height:10px;border-radius:50%;background:var(--orange)}
.how-art{left:598px;top:1616px;width:490px;height:296px;border-radius:6px;background:linear-gradient(120deg,#f4f6fc 0%,#eaf6f0 45%,#f8e6f0 100%);box-shadow:var(--card-shadow)}

/* pricing */
.pricing-title{left:0;top:2090px;width:1200px;text-align:center;font:500 25px/41px "Roboto",sans-serif}
.pricing-sub{left:0;top:2188px;width:1200px;text-align:center;font:400 14px "Open Sans",sans-serif;color:#333}
.plan{top:2255px;width:462px;height:543px;background:var(--white);border-radius:14px;box-shadow:var(--card-shadow);text-align:center}
.plan h3{margin-top:38px;font:500 25px "Roboto",sans-serif}
.plan .plan-sub{margin-top:14px;font:400 13.5px "Open Sans",sans-serif;color:#333}
.plan hr{margin:22px 46px 0;border:0;border-top:1px solid #ddd}
.plan .price{margin-top:16px;font:700 20px "Roboto",sans-serif}
.plan ul{list-style:none;position:absolute;left:112px;top:355px;text-align:left}
.plan li{position:relative;padding-left:28px;height:34px;font:400 14.5px "Open Sans",sans-serif;color:#333}
.plan li::before{content:"";position:absolute;left:0;top:4px;width:14px;height:14px;border-radius:50%;background:var(--navy)}
.plan li::after{content:"";position:absolute;left:4px;top:7px;width:5px;height:3px;border-left:2px solid #fff;border-bottom:2px solid #fff;transform:rotate(-45deg)}
.range-labels{display:flex;justify-content:space-between;margin:12px 70px 0;font:700 14px "Roboto",sans-serif}
.range{margin:12px 70px 0;height:6px;border-radius:3px;background:#dde1ee;position:relative}
.range span{position:absolute;left:0;top:0;height:6px;width:50%;border-radius:3px;background:var(--navy)}
.credits{margin-top:16px;font:400 15px "Open Sans",sans-serif}

/* faq */
.faq{left:0;top:2888px;width:1200px;height:701px;background:linear-gradient(120deg,#d8dbe8 0%,#b9bfd6 50%,#cfd3e2 100%)}
.faq-title{left:0;top:2964px;width:1200px;text-align:center;font:500 29px "Roboto",sans-serif}
.faq-item{left:167px;width:866px;background:var(--white);box-shadow:0 3px 12px rgba(30,40,90,.12);padding:0 30px}
.faq-item .q{font:500 17px "Roboto",sans-serif;color:#333;display:flex;justify-content:space-between;align-items:center;height:76px}
.faq-item .sign{font:700 22px "Roboto",sans-serif;color:#333}
.faq-item .a{font:400 12px/23px "Open Sans",sans-serif;color:#666;margin-top:-14px}

/* sites */
.sites-title{left:0;top:3672px;width:1200px;text-align:center;font:500 29px "Roboto",sans-serif}
.site-badge{top:3759px;width:158px;height:158px;border-radius:50%;background:#d8def2;display:flex;align-items:center;justify-content:center}
.site-badge span{width:136px;height:136px;border-radius:50%;background:var(--navy);color:var(--white);display:flex;align-items:center;justify-content:center;font:500 19px "Roboto",sans-serif}
.slider-dot{top:3962px;width:10px;height:10px;border-radius:50%;background:#c8c9cf}

/* footer */
.site-footer{left:0;top:4057px;width:1200px;height:371px;background:var(--footer);color:var(--white)}
.site-footer .brand{position:absolute;left:112px;top:117px;color:var(--white)}
.site-footer .brand-mark{background:var(--white)}
.social{position:absolute;top:193px;width:34px;height:34px;border-radius:50%;background:var(--orange)}
.foot-col{position:absolute;top:62px}
.foot-col h4{font:500 20px "Roboto",sans-serif;margin-bottom:14px}
.foot-col li{list-style:none;font:400 14.5px "Open Sans",sans-serif;height:26px}
.foot-col li::before{content:"»";margin-right:12px}
.contact li::before{content:none}
.contact li{display:flex;gap:10px;align-items:flex-start;line-height:24px;height:auto;margin-bottom:14px}
.copyright{position:absolute;left:0;top:305px;width:1200px;text-align:center;font:400 14px "Open Sans",sans-serif}
</style>
</head>
<body>

<header class="site-header">
  <div class="abs brand"><span class="brand-mark"></span>AnswerCraft</div>
  <a class="nav-link" style="left:414px">Why Reply?</a>
  <a class="nav-link" style="left:547px">How it works</a>
  <a class="nav-link" style="left:703px">Pricing</a>
  <a class="nav-link" style="left:808px">Blog</a>
  <a class="nav-link" style="left:892px">Login</a>
  <a class="btn" style="left:983px;top:34px;width:105px;height:47px">Try Free</a>
</header>

<section>
  <div class="abs hero" role="img" aria-label="Blurred photo of a person holding a phone, overlaid with floating review cards and star ratings"></div>
  <div class="abs hero-bubble"></div>
  <svg class="abs" style="left:600px;top:540px" width="180" height="100" viewBox="0 0 180 100" aria-hidden="true">
    <path d="M10 0 L100 0 L90 90 Q86 100 76 92 Z" fill="#fff"/>
    <path d="M30 0 L80 0 L76 68 Z" fill="var(--navy)"/>
  </svg>
  <div class="abs hero-panel">
    <h1>Write personalized<br>responses to reviews<br>in 10 seconds!</h1>
  </div>
  <a class="btn" style="left:456px;top:438px;width:146px;height:47px">Start for free</a>
  <a class="btn btn-outline" style="left:615px;top:438px;width:128px;height:47px">Learn more</a>
  <span class="abs hero-dot" style="left:569px"></span>
  <span class="abs hero-dot" style="left:586px"></span>
  <span class="abs hero-dot" style="left:603px;background:var(--orange)"></span>
  <span class="abs hero-dot" style="left:620px"></span>
</section>

<p class="abs intro">It's simple. Our tool writes replies and responses to the <span class="accent">reviews</span><br>your <span class="accent">customers leave</span>. Doesn't matter if it's 1 or 5 stars.</p>

<section>
  <div class="abs feature-card" style="left:112px">
    <h3>Improved SEO</h3>
    <p>Findly loves seeing you leave a reply to your reviews and will give you a boost in their search results and local SEO.</p>
    <a class="btn" style="left:92px;top:249px;width:117px;height:41px">Learn more</a>
  </div>
  <div class="abs feature-card" style="left:450px">
    <h3>Build Customer Trust</h3>
    <p>Customers want to know there are humans behind your companies product or service. Show them you value their feedback.</p>
    <a class="btn" style="left:92px;top:249px;width:117px;height:41px">Learn more</a>
  </div>
  <div class="abs feature-card" style="left:789px">
    <h3>Convert New Customers</h3>
    <p>FACT: Potential customers read reviews before making a decision. Give a good first impression with personalized replies.</p>
    <a class="btn" style="left:92px;top:249px;width:117px;height:41px">Learn more</a>
  </div>
  <div class="abs feature-art" style="left:132px" role="img" aria-label="Illustration of a review card with a written reply for search ranking"></div>
  <div class="abs feature-art" style="left:470px" role="img" aria-label="Illustration of a customer review with a reply building trust"></div>
  <div class="abs feature-art" style="left:809px" role="img" aria-label="Illustration of a rental listing review with a friendly reply"></div>
  <svg class="abs arrow" style="left:47px" viewBox="0 0 44 44" aria-label="Previous">
    <circle cx="22" cy="22" r="20" fill="#fff" stroke="var(--navy)" stroke-width="2"/>
    <path d="M25 14 L17 22 L25 30" fill="none" stroke="var(--navy)" stroke-width="2.5"/>
  </svg>
  <svg class="abs arrow" style="left:1114px" viewBox="0 0 44 44" aria-label="Next">
    <circle cx="22" cy="22" r="21" fill="var(--navy)"/>
    <path d="M19 14 L27 22 L19 30" fill="none" stroke="#fff" stroke-width="2.5"/>
  </svg>
</section>

<section>
  <div class="abs how" role="img" aria-label="Faded photo background with customer satisfaction stars"></div>
  <h2 class="abs how-title">How it <span class="accent">works</span></h2>
  <h3 class="abs how-sub">1 minute account creation</h3>
  <p class="abs how-text">Gain access to the most powerful tool for writing unique and personal responses to the reviews your customers leave your business.</p>
  <div class="how-point" style="top:1770px">We make it way too simple!</div>
  <div class="how-point" style="top:1856px">Only a 10 second wait</div>
  <div class="abs how-art" role="img" aria-label="Interface illustration: list of reviews, a reply editor, tone choices and a submit button"></div>
</section>

<section>
  <h2 class="abs pricing-title">Never worry about having to come up with a unique <span class="accent">response</span><br>to each <span class="accent">review</span> ever again!</h2>
  <p class="abs pricing-sub">If your business, product or service receives reviews, this tool will save you hundreds of hours.</p>

  <div class="abs plan" style="left:110px">
    <h3>Monthly Subscriptions</h3>
    <p class="plan-sub">Perfect for getting started for one business/product</p>
    <hr>
    <p class="price">Starts at $9.99 / month</p>
    <div class="range-labels"><span>50k</span><span>700k</span></div>
    <div class="range"><span></span></div>
    <p class="credits">5000 word credits</p>
    <a class="btn" style="left:162px;top:279px;width:139px;height:41px">Start for free</a>
    <ul>
      <li>Personalized responses</li>
      <li>30+ Languages</li>
      <li>Auto-Save</li>
      <li>Revision History</li>
      <li>Assign members usage limits</li>
    </ul>
  </div>

  <div class="abs plan" style="left:626px">
    <h3>Agency Subscriptions</h3>
    <p class="plan-sub">Perfect for multiple clients/products per month</p>
    <hr>
    <p class="price">Starting at $75.00 / month</p>
    <a class="btn" style="left:162px;top:279px;width:139px;height:41px">Start for free</a>
    <ul>
      <li>Everything in the Startup plan</li>
      <li>Dedicated Account Manager</li>
      <li>Onboarding &amp; Training</li>
      <li>Unlimited Integrations</li>
    </ul>
  </div>
</section>

<section>
  <div class="abs faq" role="img" aria-label="Faded background photo with customer review stars"></div>
  <h2 class="abs faq-title">Frequently asked <span class="accent">questions</span></h2>
  <div class="abs faq-item" style="top:3051px;height:146px">
    <div class="q">Why is it important to respond to Findly reviews? <span class="sign">–</span></div>
    <p class="a">Responding to Findly reviews is vital for your business's success in local search results. By responding to both negative and positive feedback, you show customers that you're committed to listening to their concerns and exceeding their expectations.</p>
  </div>
  <div class="abs faq-item" style="top:3228px"><div class="q">Why is it important to respond to negative reviews? <span class="sign">+</span></div></div>
  <div class="abs faq-item" style="top:3331px"><div class="q">How can I trust someone who doesn't work at my business to reply to reviews on my behalf? <span class="sign">+</span></div></div>
  <div class="abs faq-item" style="top:3435px"><div class="q">Which online review sites does AnswerCraft.com support? <span class="sign">+</span></div></div>
</section>

<section>
  <h2 class="abs sites-title">Write replies to the reviews you <span class="accent">get on sites like</span></h2>
  <div class="abs site-badge" style="left:120px"><span>Findly</span></div>
  <div class="abs site-badge" style="left:322px"><span>Roomhost</span></div>
  <div class="abs site-badge" style="left:523px"><span>Ratewise</span></div>
  <div class="abs site-badge" style="left:725px"><span>Marketnest</span></div>
  <div class="abs site-badge" style="left:928px"><span>Localbuzz</span></div>
  <span class="abs slider-dot" style="left:562px"></span>
  <span class="abs slider-dot" style="left:580px;background:var(--orange)"></span>
  <span class="abs slider-dot" style="left:598px"></span>
  <span class="abs slider-dot" style="left:616px"></span>
</section>

<footer class="abs site-footer">
  <div class="brand"><span class="brand-mark"></span>AnswerCraft</div>
  <span class="social" style="left:112px" aria-label="Social profile"></span>
  <span class="social" style="left:155px" aria-label="Social profile"></span>
  <span class="social" style="left:198px" aria-label="Social profile"></span>
  <span class="social" style="left:241px" aria-label="Social profile"></span>

  <div class="foot-col" style="left:431px">
    <h4>Quick Links</h4>
    <ul><li>Why Reply?</li><li>How It Works</li><li>Pricing</li><li>Blog</li></ul>
  </div>
  <div class="foot-col" style="left:639px">
    <h4>Our Company</h4>
    <ul><li>Blog</li><li>Privacy Policy</li><li>Contact</li><li>Sitemap</li></ul>
  </div>
  <div class="foot-col contact" style="left:863px">
    <h4>Contact us</h4>
    <ul>
      <li><svg width="14" height="18" viewBox="0 0 14 18" style="margin-top:4px;flex:none"><path d="M7 0a7 7 0 0 0-7 7c0 5 7 11 7 11s7-6 7-11a7 7 0 0 0-7-7z" fill="#fff"/><circle cx="7" cy="7" r="2.5" fill="#151515"/></svg><span>Lorem ipsum dolor sit<br>amet, consectetur adipiscing</span></li>
      <li><svg width="16" height="16" viewBox="0 0 16 16" style="margin-top:4px;flex:none"><path d="M3 1l3 3-2 2c1 2 3 4 6 6l2-2 3 3-2 2C7 15 1 9 1 3z" fill="#fff"/></svg><span>1+ (555) 014 2290</span></li>
      <li><svg width="16" height="12" viewBox="0 0 16 12" style="margin-top:6px;flex:none"><rect width="16" height="12" rx="1" fill="#fff"/><path d="M1 1l7 6 7-6" fill="none" stroke="#151515" stroke-width="1.5"/></svg><span>info@answercraft.com</span></li>
    </ul>
  </div>
  <p class="copyright">©Copyrights 2023 AnswerCraft &nbsp;&nbsp;| &nbsp;&nbsp;All Rights Reserved</p>
</footer>

</body>
</html>
```